Process Diagram - Circular Economy

I would like for a designer to take this rough sketch and turn it into a high quality design which can be used in a business presentation. Seeking to get both PDF and Jpeg file versions of the finished product.

Colours don't have to be the exact same as the rough sketch PDF, the green used is pretty ugly so open to some changes.

Target Market(s)

Corporate audience

Requirements
Must have
• Clear text for each party; VENOR, MORLAN, BUYER

Smaller text for the functions; marketing, recovery, logistics, cleaning, decontamination, testing & re-certification, storage, engineering suitability

```html
<!DOCTYPE html>
<html lang="en">
<head>
<meta charset="utf-8">
<title>Circular Economy Process</title>
<link href="https://fonts.googleapis.com/css2?family=Fira+Sans:wght@600&family=Roboto:wght@700&family=Roboto+Slab:wght@700&display=swap" rel="stylesheet">
<style>
  :root {
    --ink: #454545;
    --vendor: #bd9e8b;
    --buyer: #7bbfb5;
    --cycle: #4b5eab;
    --marketing: #6672b6;
    --label: #ffffff;
    --paper: #ffffff;
  }
  html, body {
    margin: 0;
    padding: 0;
    overflow: hidden;
    background: var(--paper);
  }
  .canvas {
    position: relative;
    width: 1200px;
    height: 832px;
    overflow: hidden;
    background: var(--paper);
  }
  .stage-title {
    position: absolute;
    top: 116px;
    margin: 0;
    font-family: "Roboto", Arial, sans-serif;
    font-weight: 700;
    font-size: 39px;
    color: var(--ink);
    letter-spacing: 0.5px;
    line-height: 1;
  }
  .stage-title--end { left: 115px; }
  .stage-title--new { right: 134px; }
  .flow {
    position: absolute;
    left: 0;
    top: 0;
  }
  .party {
    font-family: "Roboto Slab", Georgia, serif;
    font-weight: 700;
    font-size: 25px;
    fill: var(--label);
  }
  .party--cycle { text-anchor: end; }
  .function {
    font-family: "Fira Sans", Arial, sans-serif;
    font-weight: 600;
    font-size: 15.5px;
    fill: var(--label);
  }
</style>
</head>
<body>
<div class="canvas">
  <h1 class="stage-title stage-title--end">END OF LIFE</h1>
  <h2 class="stage-title stage-title--new">NEW LIFE</h2>

  <svg class="flow" width="1200" height="832" viewBox="0 0 1200 832" role="img" aria-label="Circular flow from vendor through the Morlan cycle to buyer">
    <defs>
      <linearGradient id="cycle-fill" gradientUnits="userSpaceOnUse" x1="490" y1="0" x2="655" y2="0">
        <stop offset="0" stop-color="var(--buyer)"/>
        <stop offset="1" stop-color="var(--cycle)"/>
      </linearGradient>
      <linearGradient id="vendor-fill" gradientUnits="userSpaceOnUse" x1="590" y1="290" x2="710" y2="395">
        <stop offset="0.15" stop-color="var(--vendor)"/>
        <stop offset="0.9" stop-color="var(--cycle)"/>
      </linearGradient>
    </defs>

    <!-- buyer band -->
    <polygon class="band band--buyer" points="595,291 958,198 1055,218 959,293 739,354" fill="var(--buyer)"/>

    <!-- cycle ring -->
    <g class="cycle-ring">
      <circle cx="596" cy="498" r="155" fill="none" stroke="url(#cycle-fill)" stroke-width="94"/>
      <path d="M596,343 A155,155 0 0 1 751,498 A155,155 0 0 1 706,608" fill="none" stroke="var(--cycle)" stroke-width="94"/>
      <path d="M441,498 A155,155 0 0 1 596,343" fill="none" stroke="var(--buyer)" stroke-width="94"/>
    </g>

    <!-- vendor band -->
    <path class="band band--vendor" fill="url(#vendor-fill)"
          d="M116,198 L595,291 L641,300 A202,202 0 0 1 770,395 L690,430 C650,400 600,380 540,362 L116,294 Z"/>

    <!-- marketing band -->
    <path class="band band--marketing" fill="var(--marketing)"
          d="M176,282 L539,359 C600,372 650,392 680,420 C696,436 702,455 702,474 C670,452 640,437 612,426 C585,416 560,410 539,408 L431,382 L176,330 Z"/>

    <!-- parties -->
    <text class="party" x="139" y="262">VENDOR</text>
    <text class="party" x="893" y="257">BUYER</text>
    <text class="party party--cycle" x="768" y="598">MORLAN</text>

    <!-- functions -->
    <text class="function" x="187" y="310" transform="rotate(12 187 310)">Marketing</text>
    <text class="function" x="565" y="341">Recovery</text>
    <text class="function" x="703" y="436">Logistics</text>
    <text class="function" x="719" y="513">Cleaning</text>
    <text class="function" x="535" y="656">Decontamination</text>
    <text class="function" x="417" y="569">Testing &amp;</text>
    <text class="function" x="417" y="589">Re-certification</text>
    <text class="function" x="412" y="513">Storage</text>
    <text class="function" x="418" y="427">Engineering</text>
    <text class="function" x="418" y="446">Suitability</text>
  </svg>
</div>
</body>
</html>
```